Medical centre needs a business card

We are a medcial centre in Australia, needing a new business card. Our demographic is low working class families. We are going to be renovating our premises to modernise the look and also had a new logo done a few months ago representing quality and community, and now need to update our cards. It needs to be doubled sided, with logo and contact details on the front, and appointment details on the back. . Needs to be modern and simple, easy to read. <br/><br/>Name: Kindle Grove Medical Centre <br/>Address: 512 Parmley Rd (Cnr Parmley Rd & Osgood Creek Rd),<br/>Tindarra Court Shopping Centre, Paralowie, SA 5108<br/>Ph: 08 8461 3072<br/>Tag line: Where your wellbeing comes first<br/>Website: www.kindlegrovemedicalcentre-example.com.au<br/>Online bookings also available<br/><br/>(On the back, to have 3 lines of appointments that can be written in.<br/>Day, date, time)<br/><br/>Your next appointment is on<br/>Can try “M T W Th F Sa Su _________________ at ____________ am/pm” or other combinations <br/>Please advise as soon as possible if unable to attend<br/>Cancellation fees apply if less than 2 hrs notice<br/>Online appointments available (please highlight this option by either by position, colour or font)

Target Market(s)

Lower social economic working class, young families to seniors

Industry/Entity Type

Medical Centre

Contact Information for Business Card

Kindle Grove Medical Centre
512 Parmley Rd (Cnr Parmley Rd & Osgood Creek Drive)
Tindarra Court Shopping Centre
Brenlow Heights SA 5990
Ph: 08 8461 3072
www.kindlegrovemedicalcentre-example.com.au
Tagline line: where your wellbeing comes first
Back side is for appointments
Your next appointment is with Dr ______________
Day/date/time (Please give 3 lines of appointments)
Please advise as soon as possible if unable to attend
Cancellation fees apply if less than 2 hours notice
Online appointments available
Book online easily and conveniently (please highlight online appointments)

Font styles to use
Serif
Sans Serif

Colors

Designer to choose colors to be used in the design.

Requirements
Must have
• Modern and simple
• Easy to ready
• Induces a wellbeing feeling
• Incorporate our logo colours and feel from logo
• Induces feeling of stability and security
Nice to have
• Attract attention
• Pleasant to look at
• Feeling of innovation
Should not have
• Loud clashing colours
• Overly luxurious feeling
• Overly artistic

```html
<!DOCTYPE html>
<html lang="en">
<head>
<meta charset="utf-8">
<title>Kindle Grove Medical Centre – Business Card</title>
<link href="https://fonts.googleapis.com/css2?family=Josefin+Sans:wght@600;700&family=Work+Sans:wght@400;500&display=swap" rel="stylesheet">
<style>
  :root {
    --brand-blue: #0a6dbd;
    --brand-green: #a3cd48;
    --card-white: #ffffff;
    --text-grey: #6b6b6b;
    --rule-grey: #7a7a7a;
    --backdrop: #2b2b2b;
  }
  html, body {
    margin: 0;
    width: 1200px;
    height: 900px;
    overflow: hidden;
    background: var(--backdrop);
  }
  .card {
    position: absolute;
    left: 261px;
    width: 656px;
    height: 357px;
    border-radius: 30px;
    background: var(--card-white);
    overflow: hidden;
  }
  .card-front { top: 69px; }
  .card-back { top: 472px; }

  /* Front */
  .brand {
    position: absolute;
    top: 40px;
    left: 0;
    width: 100%;
    height: 107px;
    display: flex;
    justify-content: center;
    align-items: center;
    gap: 28px;
    padding-left: 8px;
    box-sizing: border-box;
  }
  .brand-dot {
    width: 96px;
    height: 96px;
    border-radius: 50%;
    background: var(--brand-green);
  }
  .brand-name {
    font-family: "Josefin Sans", sans-serif;
    font-weight: 700;
    color: var(--brand-blue);
    line-height: 1.05;
    text-align: center;
  }
  .brand-name .line-main { display: block; font-size: 36px; letter-spacing: 1px; }
  .brand-name .line-sub { display: block; font-size: 15px; letter-spacing: 5.4px; margin-top: 4px; }

  .accent-band {
    position: absolute;
    top: 198px;
    left: 0;
    width: 100%;
    height: 13px;
    background: var(--brand-green);
  }
  .contact-panel {
    position: absolute;
    top: 211px;
    left: 0;
    width: 100%;
    bottom: 0;
    background: var(--brand-blue);
  }
  .contact-icons {
    position: absolute;
    top: 180px;
    left: 0;
    width: 100%;
    display: flex;
    justify-content: center;
    gap: 4px;
  }
  .contact-icon {
    width: 34px;
    height: 34px;
    border-radius: 50%;
    background: var(--card-white);
    border: 2px solid var(--card-white);
    display: flex;
    align-items: center;
    justify-content: center;
  }
  .contact-icon svg { width: 32px; height: 32px; }

  .contact-lines {
    position: absolute;
    left: 0;
    width: 100%;
    margin: 0;
    text-align: center;
    font-family: "Josefin Sans", sans-serif;
    font-weight: 600;
    color: var(--card-white);
    text-transform: uppercase;
  }
  .contact-phone { top: 238px; font-size: 16px; letter-spacing: 1.8px; }
  .contact-web { top: 261px; font-size: 14px; letter-spacing: 1.2px; }
  .contact-address { top: 294px; font-size: 15.5px; letter-spacing: 1.2px; line-height: 23px; }

  /* Back */
  .tagline {
    position: absolute;
    top: 33px;
    left: 0;
    width: 100%;
    margin: 0;
    text-align: center;
    font-family: "Josefin Sans", sans-serif;
    font-weight: 600;
    font-size: 23px;
    letter-spacing: 1px;
    color: var(--brand-blue);
    text-transform: uppercase;
  }
  .appointment {
    position: absolute;
    left: 105px;
    width: 444px;
    font-family: "Work Sans", sans-serif;
    display: flex;
    align-items: flex-end;
    gap: 6px;
  }
  .appointment .label { white-space: nowrap; }
  .appointment .write-line {
    flex: 1;
    border-bottom: 1px solid var(--rule-grey);
    height: 14px;
  }
  .appointment-doctor { top: 100px; font-size: 16px; font-weight: 500; color: var(--brand-blue); letter-spacing: 0.6px; width: 428px; }
  .appointment-doctor .write-line { border-color: var(--brand-blue); }
  .appointment-field { font-size: 16px; color: var(--text-grey); letter-spacing: 0.5px; }
  .field-day { top: 141px; }
  .field-date { top: 181px; }
  .field-time { top: 221px; }

  .notice {
    position: absolute;
    top: 276px;
    left: 0;
    width: 100%;
    margin: 0;
    text-align: center;
    font-family: "Work Sans", sans-serif;
    font-size: 16px;
    line-height: 20px;
    letter-spacing: 0.8px;
    color: var(--text-grey);
  }
  .notice .online { color: var(--brand-green); font-weight: 500; }
</style>
</head>
<body>

<section class="card card-front" aria-label="Business card front">
  <div class="brand">
    <span class="brand-dot"></span>
    <span class="brand-name">
      <span class="line-main">KINDLE GROVE</span>
      <span class="line-sub">MEDICAL CENTRE</span>
    </span>
  </div>

  <div class="accent-band"></div>
  <div class="contact-panel"></div>

  <div class="contact-icons">
    <span class="contact-icon" aria-label="Phone">
      <svg viewBox="0 0 30 30"><circle cx="15" cy="15" r="13" fill="none" stroke="#a3cd48" stroke-width="1.6"/><path d="M11 8.5l2.2-.6 1.3 3.3-1.5 1c.6 1.8 1.6 3.1 3 4.2l1.3-1.2 3 1.8-.8 2.2c-4.6.3-9.4-6.1-8.5-10.7z" fill="none" stroke="#0a6dbd" stroke-width="1.4" stroke-linejoin="round"/></svg>
    </span>
    <span class="contact-icon" aria-label="Website">
      <svg viewBox="0 0 30 30"><circle cx="15" cy="15" r="13" fill="none" stroke="#a3cd48" stroke-width="1.6"/><g fill="none" stroke="#0a6dbd" stroke-width="1.1"><circle cx="15" cy="15" r="7"/><ellipse cx="15" cy="15" rx="3" ry="7"/><path d="M8 15h14M9 11.5h12M9 18.5h12M15 8v14"/></g></svg>
    </span>
    <span class="contact-icon" aria-label="Location">
      <svg viewBox="0 0 30 30"><circle cx="15" cy="15" r="13" fill="none" stroke="#a3cd48" stroke-width="1.6"/><path d="M15 7.5a5 5 0 0 0-5 5c0 3.6 5 9.5 5 9.5s5-5.9 5-9.5a5 5 0 0 0-5-5z" fill="#0a6dbd"/><circle cx="15" cy="12.5" r="1.8" fill="#fff"/></svg>
    </span>
  </div>

  <p class="contact-lines contact-phone">08 8461 3072</p>
  <p class="contact-lines contact-web">www.kindlegrovemedicalcentre-example.com.au</p>
  <p class="contact-lines contact-address">512 Parmley Rd (Cnr Parmley Rd &amp; Osgood Creek Drive)<br>Tindarra Court Shopping Centre Brenlow Heights SA 5990</p>
</section>

<section class="card card-back" aria-label="Business card back">
  <h2 class="tagline">Where your wellbeing comes first</h2>

  <div class="appointment appointment-doctor"><span class="label">Your next appointment is with Dr</span><span class="write-line"></span></div>
  <div class="appointment appointment-field field-day"><span class="label">Day</span><span class="write-line"></span></div>
  <div class="appointment appointment-field field-date"><span class="label">date</span><span class="write-line"></span></div>
  <div class="appointment appointment-field field-time"><span class="label">time</span><span class="write-line"></span></div>

  <p class="notice">Please advise as soon as possible if unable to attend<br>Cancellation fees apply if less than 2 hours notice<br><span class="online">Online appointments available.</span></p>
</section>

</body>
</html>
```